LM-Steuerberatung WordPress Site fully implemented (tax advisor)

Hello!
I need a little Wordpress Site for my newly founded Tax-Advisor Company.
I am a one-man Office advising in the area of Crypto-Currency.
PLEASE only provide a Design, if you can also Implement a WP-Site afterwards on an existing Webspace.

Please find the Content and Website-Description in the attached Document

Language for the Website is German (for now)

Target Market(s)

Tax-Advisory (specialized in Crypto Currency)

Coding

Coded - Design and coding required

Number of Pages Required

5+ page

Font styles to use
Sans Serif

Requirements
Must have
• Wordpress Implementation afterwards - Details according to attached Project Information Document

```html
<!DOCTYPE html>
<html lang="de">
<head>
<meta charset="utf-8">
<title>LM-Steuerberatung – Webdesign</title>
<link href="https://fonts.googleapis.com/css2?family=Manrope:wght@300;400;500;600;700;800&display=swap" rel="stylesheet">
<style>
:root{
  --navy:#1b2333;
  --navy-2:#222c40;
  --ink:#1f2430;
  --muted:#4a5160;
  --line:#d7dbe3;
  --white:#ffffff;
  --accent:#2f63c9;
}
*{box-sizing:border-box;margin:0;padding:0}
html,body{width:678px;height:1200px;overflow:hidden;background:var(--white)}
body{position:relative;font-family:'Manrope',sans-serif;color:var(--ink)}
.page{position:absolute;width:307px;background:var(--white);box-shadow:0 0 3px rgba(0,0,0,.18);overflow:hidden}
.p-home{left:19.5px;top:15px;height:351px}
.p-slider{left:19.5px;top:379px;height:351px}
.p-kolleg{left:19.5px;top:741px;height:430px}
.p-leist{left:351px;top:15px;height:406px}
.p-about{left:351px;top:437px;height:449px}

.topbar{height:13px;background:var(--navy);display:flex;align-items:center;justify-content:space-between;padding:0 25px;color:var(--white);font-size:3.6px}
.social{display:flex;gap:3px;align-items:center}
.social i{display:block;width:3px;height:3px;border-radius:50%;background:var(--white)}
.contacts{display:flex;gap:4px;align-items:center}
.contacts span{display:flex;align-items:center;gap:1.5px}
.contacts svg{width:3.6px;height:3.6px}

.nav{height:23px;display:flex;align-items:center;justify-content:space-between;padding:0 25px;border-bottom:.5px solid var(--line)}
.brand{display:flex;align-items:center;gap:2.5px;font-weight:800;font-size:4.6px;letter-spacing:.15px;color:var(--navy)}
.brand i{display:block;width:6px;height:6px;background:var(--navy)}
.menu{display:flex;align-items:center;gap:11px;font-size:3.9px;color:var(--ink)}
.menu .on{position:relative}
.menu .on::after{content:"";position:absolute;left:50%;top:6px;width:1.4px;height:1.4px;margin-left:-.7px;border-radius:50%;background:var(--navy)}
.btn-kontakt{background:var(--navy);color:var(--white);padding:3px 9px;border-radius:3px;font-weight:600}

.photo{display:block}
.banner{height:59px;position:relative;display:flex;align-items:center;justify-content:center}
.banner h1{position:relative;color:var(--white);font-size:9.5px;font-weight:600;letter-spacing:.2px}
.banner .photo{position:absolute;inset:0}

.hero{height:138px;position:relative}
.hero .photo{position:absolute;inset:0}
.hero-copy{position:absolute;left:26px;top:36px;color:var(--white)}
.hero-copy .h-light{font-size:9.6px;font-weight:400;line-height:1.35}
.hero-copy .h-bold{font-size:9.6px;font-weight:700;line-height:1.3}
.hero-copy p{font-size:4.4px;line-height:1.9;margin-top:3px;width:120px}
.btn-ghost{display:inline-flex;align-items:center;gap:2px;margin-top:7px;border:.8px solid var(--white);border-radius:4px;padding:3.2px 6px;font-size:4.2px;font-weight:600;color:var(--white)}
.dot-arrow{display:inline-block;width:3.6px;height:3.6px;border-radius:50%;background:currentColor;position:relative}
.dot-arrow::after{content:"";position:absolute;left:1px;top:1.1px;width:1.1px;height:1.1px;border-right:.5px solid var(--navy);border-top:.5px solid var(--navy);transform:rotate(45deg)}
.btn-ghost .dot-arrow::after,.btn-solid .dot-arrow::after{border-color:var(--navy)}

.slide-copy{position:absolute;left:0;right:0;top:40px;text-align:center;color:var(--white)}
.slide-copy .s1{font-size:6.4px;font-weight:500}
.slide-copy .s2{font-size:13px;font-weight:700;margin-top:1px}
.slide-copy p{font-size:4.4px;line-height:1.9;width:160px;margin:2px auto 0}
.btn-solid{display:inline-flex;align-items:center;gap:2.5px;background:var(--navy);color:var(--white);border-radius:5px;padding:3.5px 7px;font-size:4.2px;font-weight:600}
.slide-copy .btn-solid{margin-top:4px}
.slide-arrow{position:absolute;top:64px;width:6px;height:10px}
.slide-arrow.l{left:26px}.slide-arrow.r{right:26px}
.slide-dots{position:absolute;left:50%;bottom:10px;margin-left:-18px;display:flex;gap:2px}
.slide-dots i{display:block;width:10px;height:.8px;background:rgba(255,255,255,.6)}
.slide-dots i:first-child{background:var(--white)}

.features{height:78px;display:grid;grid-template-columns:repeat(3,1fr);gap:6px;padding:20px 25px 0}
.feature{display:flex;gap:4px;align-items:flex-start}
.feature .num{flex:none;width:14px;height:30px;background:var(--navy);color:var(--white);font-size:5px;font-weight:700;display:flex;align-items:center;justify-content:center}
.feature p{font-size:3.6px;line-height:1.6;color:var(--muted);padding-top:4px}

.footer{height:98px;background:var(--navy);color:var(--white);padding:17px 25px 0;position:relative}
.foot-grid{display:grid;grid-template-columns:105px 78px 1fr;height:60px}
.foot-brand .brand{color:var(--white);font-size:5.4px}
.foot-brand .brand i{background:var(--white);width:7px;height:7px}
.foot-brand p{font-size:3.8px;line-height:1.75;margin-top:6px;opacity:.9}
.foot-brand .social{margin-top:7px;gap:5px}
.foot-brand .social i{width:4px;height:4px}
.foot-col{border-left:.5px solid rgba(255,255,255,.25);padding-left:25px}
.foot-col + .foot-col{padding-left:22px}
.foot-col h4{font-size:4.1px;font-weight:700;margin-bottom:4px}
.foot-col li{list-style:none;font-size:3.9px;line-height:2.55;opacity:.9;display:flex;align-items:center;gap:2px}
.foot-col svg{width:3.6px;height:3.6px}
.copy{position:absolute;left:25px;right:25px;bottom:6px;border-top:.5px solid rgba(255,255,255,.25);padding-top:6px;text-align:center;font-size:3.3px;opacity:.9}
.copy b{font-weight:700}

.leist-body{height:212px;padding:20px 25px 0}
.intro{font-size:4px;line-height:1.75;color:var(--muted)}
.leist-row{display:flex;gap:10px;margin-top:13px}
.leist-row .photo{flex:none;width:111px;height:104px;border-radius:6px}
.checks{list-style:none;padding-top:3px}
.checks li{position:relative;padding-left:4px;font-size:3.8px;line-height:1.7;color:var(--muted);margin-bottom:2.5px}
.checks li::before{content:"";position:absolute;left:0;top:1.7px;width:1.2px;height:1.2px;border-right:.5px solid var(--ink);border-top:.5px solid var(--ink);transform:rotate(45deg)}
.leist-body .outro{margin-top:10px}
.leist-body .btn-solid{margin-top:5px;border-radius:4px}

.about-body{height:255px;padding:15px 25px 0}
.about-row{display:flex;gap:7px}
.portrait{flex:none;width:82px;text-align:center}
.portrait .photo{width:82px;height:88px;border-radius:5px;border:.6px solid var(--line)}
.portrait h3{font-size:5px;font-weight:700;margin-top:5px}
.about-text p{font-size:3.8px;line-height:1.7;color:var(--muted);margin-bottom:2.4px}
.cv{display:grid;grid-template-columns:1fr 1fr;gap:6px;margin-top:20px}
.cv-box{position:relative;border:.6px solid var(--navy);border-radius:4px;height:68px;padding:12px 5px 0}
.cv-box h5{position:absolute;top:-5px;left:50%;transform:translateX(-50%);background:var(--white);border:.6px solid var(--navy);border-radius:4px;padding:1.8px 6px;font-size:3.7px;font-weight:600;white-space:nowrap}
.cv-box p{font-size:3.6px;line-height:1.6;color:var(--muted);margin-bottom:2.6px}
.cv-box b{color:var(--ink);font-weight:700}
.about-body .btn-solid{margin:16px 0 0 2px;border-radius:4px}

.kolleg-body{height:237px;padding:19px 25px 0}
.kolleg-body .lead{font-size:4px;line-height:1.85;font-weight:600;color:var(--ink)}
.kolleg-body .intro{margin-top:2px;line-height:1.85}
.kolleg-body .photo{width:256px;height:122px;border-radius:7px;margin-top:15px}
.kolleg-body .btn-solid{margin-top:8px;border-radius:5px}

.thanks{position:absolute;left:351px;width:307px;top:956px;text-align:center;color:#1c1c1c}
.thanks .t1{font-size:39px;font-weight:400;letter-spacing:-.6px;line-height:1.05}
.thanks .t2{font-size:42px;font-weight:800;letter-spacing:-.6px;line-height:1.05}
</style>
</head>
<body>

<!-- Startseite -->
<section class="page p-home">
  <div class="topbar">
    <div class="social"><i></i><i></i><i></i></div>
    <div class="contacts">
      <span><svg viewBox="0 0 10 10"><path fill="#fff" d="M2 1l2 2-1 1.3c.6 1.2 1.5 2.1 2.7 2.7L7 6l2 2-1.2 1.3C4.5 9 1 5.5.7 2.2z"/></svg>+43 512 000 417</span>
      <span><svg viewBox="0 0 10 10"><rect x="0" y="2" width="10" height="6.5" fill="#fff"/><path d="M0 2l5 3.5L10 2" stroke="#1b2333" fill="none"/></svg>office@lm-steuer.example</span>
    </div>
  </div>
  <header class="nav">
    <div class="brand"><i></i>LM STEUERBERATUNG</div>
    <nav class="menu"><span class="on">Home</span><span>Leistungen</span><span>Über mich</span><span>Impressum</span><span class="btn-kontakt">Kontakt</span></nav>
  </header>
  <div class="hero">
    <div class="photo" role="img" aria-label="Beraterin im Büro, dunkel überlagert" style="background:linear-gradient(90deg,#1a1c22 0%,#2a2c32 45%,#3c3f47 70%,#2c3038 100%)"></div>
    <div class="hero-copy">
      <div class="h-light">WILLKOMMEN</div>
      <div class="h-bold">BEI LM-STEUERBERATUNG!</div>
      <p>Ihrem Spezialisten bei allen steuerlichen Themen rund um Einkünfte &amp; Vermögen aus Krypto-Assets.</p>
      <span class="btn-ghost">Weiter zu unseren Leistungen <span class="dot-arrow"></span></span>
    </div>
  </div>
  <div class="features">
    <div class="feature"><span class="num">01</span><p>Dann mach ich eine Schweizer Holding-Gesellschaft– dort zahlt man fast keine Steuern</p></div>
    <div class="feature"><span class="num">02</span><p>Dann melde ich einfach meinen Hauptwohnsitz in Österreich ab</p></div>
    <div class="feature"><span class="num">03</span><p>Dann lass ich meine Kryptos auf einer Börse in Singapur, dort ist das steuerfrei</p></div>
  </div>
  <footer class="footer">
    <div class="foot-grid">
      <div class="foot-brand"><div class="brand"><i></i>LM STEUERBERATUNG</div><p>Ihrem Spezialisten bei allen steuerlichen Themen rund um Einkünfte &amp; Vermögen aus Krypto-Assets.</p><div class="social"><i></i><i></i><i></i></div></div>
      <div class="foot-col"><h4>QUICK LINKS</h4><ul><li>Home</li><li>Leistungen</li><li>Über mich</li><li>Impressum</li><li>Kontakt</li></ul></div>
      <div class="foot-col"><h4>CONTACT US</h4><ul><li><svg viewBox="0 0 10 10"><rect y="2" width="10" height="6.5" fill="#fff"/></svg>office@lm-steuer.example</li><li><svg viewBox="0 0 10 10"><path fill="#fff" d="M2 1l2 2-1 1.3c.6 1.2 1.5 2.1 2.7 2.7L7 6l2 2-1.2 1.3C4.5 9 1 5.5.7 2.2z"/></svg>+43 512 000 417</li></ul></div>
    </div>
    <div class="copy">© 2022 <b>LM-Steuerberatung</b>. All right reserved</div>
  </footer>
</section>

<!-- Startseite Slider -->
<section class="page p-slider">
  <div class="topbar">
    <div class="social"><i></i><i></i><i></i></div>
    <div class="contacts">
      <span><svg viewBox="0 0 10 10"><path fill="#fff" d="M2 1l2 2-1 1.3c.6 1.2 1.5 2.1 2.7 2.7L7 6l2 2-1.2 1.3C4.5 9 1 5.5.7 2.2z"/></svg>+43 512 000 417</span>
      <span><svg viewBox="0 0 10 10"><rect x="0" y="2" width="10" height="6.5" fill="#fff"/><path d="M0 2l5 3.5L10 2" stroke="#1b2333" fill="none"/></svg>office@lm-steuer.example</span>
    </div>
  </div>
  <header class="nav">
    <div class="brand"><i></i>LM STEUERBERATUNG</div>
    <nav class="menu"><span class="on">Home</span><span>Leistungen</span><span>Über mich</span><span>Impressum</span><span class="btn-kontakt">Kontakt</span></nav>
  </header>
  <div class="hero">
    <div class="photo" role="img" aria-label="Beratungsgespräch im Team am Tisch, abgedunkelt" style="background:linear-gradient(90deg,#4a4640 0%,#6e6a66 40%,#8a8d94 65%,#5d6470 100%)"></div>
    <div class="slide-copy">
      <div class="s1">Willkommen</div>
      <div class="s2">bei LM-Steuerberatung!</div>
      <p>Ihrem Spezialisten bei allen steuerlichen Themen rund um Einkünfte &amp; Vermögen aus Krypto-Assets.</p>
      <span class="btn-solid">Weiter zu unseren Leistungen <span class="dot-arrow" style="color:#fff"></span></span>
    </div>
    <svg class="slide-arrow l" viewBox="0 0 6 10"><path d="M5 1L1 5l4 4" stroke="#fff" stroke-width="1.3" fill="none"/></svg>
    <svg class="slide-arrow r" viewBox="0 0 6 10"><path d="M1 1l4 4-4 4" stroke="#fff" stroke-width="1.3" fill="none"/></svg>
    <div class="slide-dots"><i></i><i></i><i></i></div>
  </div>
  <div class="features">
    <div class="feature"><span class="num">01</span><p>Dann mach ich eine Schweizer Holding-Gesellschaft– dort zahlt man fast keine Steuern</p></div>
    <div class="feature"><span class="num">02</span><p>Dann melde ich einfach meinen Hauptwohnsitz in Österreich ab</p></div>
    <div class="feature"><span class="num">03</span><p>Dann lass ich meine Kryptos auf einer Börse in Singapur, dort ist das steuerfrei</p></div>
  </div>
  <footer class="footer">
    <div class="foot-grid">
      <div class="foot-brand"><div class="brand"><i></i>LM STEUERBERATUNG</div><p>Ihrem Spezialisten bei allen steuerlichen Themen rund um Einkünfte &amp; Vermögen aus Krypto-Assets.</p><div class="social"><i></i><i></i><i></i></div></div>
      <div class="foot-col"><h4>QUICK LINKS</h4><ul><li>Home</li><li>Leistungen</li><li>Über mich</li><li>Impressum</li><li>Kontakt</li></ul></div>
      <div class="foot-col"><h4>CONTACT US</h4><ul><li><svg viewBox="0 0 10 10"><rect y="2" width="10" height="6.5" fill="#fff"/></svg>office@lm-steuer.example</li><li><svg viewBox="0 0 10 10"><path fill="#fff" d="M2 1l2 2-1 1.3c.6 1.2 1.5 2.1 2.7 2.7L7 6l2 2-1.2 1.3C4.5 9 1 5.5.7 2.2z"/></svg>+43 512 000 417</li></ul></div>
    </div>
    <div class="copy">© 2022 <b>LM-Steuerberatung</b>. All right reserved</div>
  </footer>
</section>

<!-- Kollegendienst -->
<section class="page p-kolleg">
  <div class="topbar">
    <div class="social"><i></i><i></i><i></i></div>
    <div class="contacts">
      <span><svg viewBox="0 0 10 10"><path fill="#fff" d="M2 1l2 2-1 1.3c.6 1.2 1.5 2.1 2.7 2.7L7 6l2 2-1.2 1.3C4.5 9 1 5.5.7 2.2z"/></svg>+43 512 000 417</span>
      <span><svg viewBox="0 0 10 10"><rect x="0" y="2" width="10" height="6.5" fill="#fff"/><path d="M0 2l5 3.5L10 2" stroke="#1b2333" fill="none"/></svg>office@lm-steuer.example</span>
    </div>
  </div>
  <header class="nav">
    <div class="brand"><i></i>LM STEUERBERATUNG</div>
    <nav class="menu"><span>Home</span><span class="on">Leistungen</span><span>Über mich</span><span>Impressum</span><span class="btn-kontakt">Kontakt</span></nav>
  </header>
  <div class="banner">
    <div class="photo" role="img" aria-label="Besprechungstisch von oben mit Unterlagen" style="background:linear-gradient(90deg,#2b2620 0%,#4a3d30 40%,#6b6257 70%,#8d8a84 100%)"></div>
    <h1>KOLLEGENDIENST</h1>
  </div>
  <div class="kolleg-body">
    <p class="lead">Ihr Fokus liegt in der traditionellen Steuerberatung und Sie haben keine Zeit sich das hochkomplexe Spezialthema Kryptowährungen etc. einzuarbeiten?</p>
    <p class="intro">Um Ihre Klienten dennoch weiterhin vollumfänglich beraten zu können, biete ich Ihnen gerne mein Know-How und die gesamte Leistungspalette an um Ihre Kunden ganz nach Ihrem Wunsch entweder direkt oder diskret im Hintergrund bei sämtlichen Themen rund um Krypto mit steuerlicher Expertise dazu zu unterstützen.</p>
    <div class="photo" role="img" aria-label="Gruppenfoto eines Beraterteams" style="background:linear-gradient(180deg,#d8cfc3 0%,#b7b0a8 50%,#5d6a83 100%)"></div>
    <span class="btn-solid">Nehmen sie gerne Kontakt mit mir auf! <span class="dot-arrow" style="color:#fff"></span></span>
  </div>
  <footer class="footer">
    <div class="foot-grid">
      <div class="foot-brand"><div class="brand"><i></i>LM STEUERBERATUNG</div><p>Ihrem Spezialisten bei allen steuerlichen Themen rund um Einkünfte &amp; Vermögen aus Krypto-Assets.</p><div class="social"><i></i><i></i><i></i></div></div>
      <div class="foot-col"><h4>QUICK LINKS</h4><ul><li>Home</li><li>Leistungen</li><li>Über mich</li><li>Impressum</li><li>Kontakt</li></ul></div>
      <div class="foot-col"><h4>CONTACT US</h4><ul><li><svg viewBox="0 0 10 10"><rect y="2" width="10" height="6.5" fill="#fff"/></svg>office@lm-steuer.example</li><li><svg viewBox="0 0 10 10"><path fill="#fff" d="M2 1l2 2-1 1.3c.6 1.2 1.5 2.1 2.7 2.7L7 6l2 2-1.2 1.3C4.5 9 1 5.5.7 2.2z"/></svg>+43 512 000 417</li></ul></div>
    </div>
    <div class="copy">© 2022 <b>LM-Steuerberatung</b>. All right reserved</div>
  </footer>
</section>

<!-- Leistungen -->
<section class="page p-leist">
  <div class="topbar">
    <div class="social"><i></i><i></i><i></i></div>
    <div class="contacts">
      <span><svg viewBox="0 0 10 10"><path fill="#fff" d="M2 1l2 2-1 1.3c.6 1.2 1.5 2.1 2.7 2.7L7 6l2 2-1.2 1.3C4.5 9 1 5.5.7 2.2z"/></svg>+43 512 000 417</span>
      <span><svg viewBox="0 0 10 10"><rect x="0" y="2" width="10" height="6.5" fill="#fff"/><path d="M0 2l5 3.5L10 2" stroke="#1b2333" fill="none"/></svg>office@lm-steuer.example</span>
    </div>
  </div>
  <header class="nav">
    <div class="brand"><i></i>LM STEUERBERATUNG</div>
    <nav class="menu"><span>Home</span><span class="on">Leistungen</span><span>Über mich</span><span>Impressum</span><span class="btn-kontakt">Kontakt</span></nav>
  </header>
  <div class="banner">
    <div class="photo" role="img" aria-label="Hände mit Stift und Laptop mit Diagrammen" style="background:linear-gradient(90deg,#2a2d33 0%,#5a5e66 45%,#8b8f96 75%,#6a6e75 100%)"></div>
    <h1>LEISTUNGEN</h1>
  </div>
  <div class="leist-body">
    <p class="intro">Ich biete in meiner Kanzlei ausschließlich Spezialberatung rund um die komplexen und vielseitigen Themen im Krypto-Bereich sowie deren Besteuerung, bzw. der Besteuerung und steuerlichen Optimierung von anderen passiven Einkommensmodellen an:</p>
    <div class="leist-row">
      <div class="photo" role="img" aria-label="Hand unterschreibt Dokument vor blauen Finanzgrafiken" style="background:linear-gradient(135deg,#0b2a7a 0%,#1f5fd6 50%,#5aa8f0 100%)"></div>
      <ul class="checks">
        <li>Steueroptimales Besitzen von KryptoAssets auf in- und ausländischen Börsen</li>
        <li>Hilfestellung bei der Dokumentation der Einkünfte (Verwendung von Tax-Tools und Aufbereitung der Daten, etc.)</li>
        <li>Finanzstrafrechtliche Offenlegung und Aufarbeitung bei Einkünften die nicht ordnungsgemäß erklärt wurden</li>
        <li>Beratung rund um das Thema Wegzug, Wohnsitzverlegung und in-/ausländische Gesellschaften</li>
        <li>Hilfe bei der korrekten Erklärung der Crypto-Einkünfte und Erstellung der Steuererklärungen</li>
        <li>Beratung bei der Unterscheidung und Besteuerung der diversen</li>
        <li>Einkunftsmöglichkeiten (Trading, Staking, Lending, Mining, Nodes, NFTs, etc.)</li>
      </ul>
    </div>
    <p class="intro outro">Werden neben der Spezialberatung auch noch klassische Services wie Buchhaltung, Lohnverrechnung etc. benötigt, kann dies gerne über Partner-Kanzleien von mir organisiert werden.</p>
    <span class="btn-solid">Nehmen sie gerne Kontakt mit mir auf! <span class="dot-arrow" style="color:#fff"></span></span>
  </div>
  <footer class="footer">
    <div class="foot-grid">
      <div class="foot-brand"><div class="brand"><i></i>LM STEUERBERATUNG</div><p>Ihrem Spezialisten bei allen steuerlichen Themen rund um Einkünfte &amp; Vermögen aus Krypto-Assets.</p><div class="social"><i></i><i></i><i></i></div></div>
      <div class="foot-col"><h4>QUICK LINKS</h4><ul><li>Home</li><li>Leistungen</li><li>Über mich</li><li>Impressum</li><li>Kontakt</li></ul></div>
      <div class="foot-col"><h4>CONTACT US</h4><ul><li><svg viewBox="0 0 10 10"><rect y="2" width="10" height="6.5" fill="#fff"/></svg>office@lm-steuer.example</li><li><svg viewBox="0 0 10 10"><path fill="#fff" d="M2 1l2 2-1 1.3c.6 1.2 1.5 2.1 2.7 2.7L7 6l2 2-1.2 1.3C4.5 9 1 5.5.7 2.2z"/></svg>+43 512 000 417</li></ul></div>
    </div>
    <div class="copy">© 2022 <b>LM-Steuerberatung</b>. All right reserved</div>
  </footer>
</section>

<!-- Über mich -->
<section class="page p-about">
  <div class="topbar">
    <div class="social"><i></i><i></i><i></i></div>
    <div class="contacts">
      <span><svg viewBox="0 0 10 10"><path fill="#fff" d="M2 1l2 2-1 1.3c.6 1.2 1.5 2.1 2.7 2.7L7 6l2 2-1.2 1.3C4.5 9 1 5.5.7 2.2z"/></svg>+43 512 000 417</span>
      <span><svg viewBox="0 0 10 10"><rect x="0" y="2" width="10" height="6.5" fill="#fff"/><path d="M0 2l5 3.5L10 2" stroke="#1b2333" fill="none"/></svg>office@lm-steuer.example</span>
    </div>
  </div>
  <header class="nav">
    <div class="brand"><i></i>LM STEUERBERATUNG</div>
    <nav class="menu"><span>Home</span><span>Leistungen</span><span class="on">Über mich</span><span>Impressum</span><span class="btn-kontakt">Kontakt</span></nav>
  </header>
  <div class="banner">
    <div class="photo" role="img" aria-label="Hand mit Münze neben Tastatur, dunkel" style="background:linear-gradient(90deg,#1e2024 0%,#34363b 50%,#4a4b4e 75%,#2a2b2e 100%)"></div>
    <h1>ÜBER MICH</h1>
  </div>
  <div class="about-body">
    <div class="about-row">
      <div class="portrait">
        <div class="photo" role="img" aria-label="Porträt des Steuerberaters im Anzug" style="background:linear-gradient(180deg,#d9dadc 0%,#b9bbbe 55%,#2a2c30 100%)"></div>
        <h3>Mag. Lukas Marten</h3>
      </div>
      <div class="about-text">
        <p>Mag. Lukas Marten Ich blicke auf eine sehr umfassende Ausbildung und langjährige Berufserfahrung in der IT Branche zurück. Nach Abschluss des Wirtschaftsstudiums habe ich den klassischen Weg der</p>
        <p>Steuerberaterausbildung absolviert und bin in diesem Bereich seit über 13 Jahren beratend tätig.</p>
        <p>Durch die Kombination meines umfassenden Wissens in der IT und der Wirtschaft habe ich schon immer gerne Unternehmen mit besonderes technischen oder digitalen Geschäftsmodellen beraten. Seit mehreren Jahren bin ich privat an der</p>
        <p>Blockchaintechnologie und dem Krypto-Universum interessiert und bereits seit dem Jahre 2017 ist dieses Thema auch Teil meiner fixen Beratungsfelder in der Steuerberatung.</p>
      </div>
    </div>
    <div class="cv">
      <div class="cv-box"><h5>AUSBILDUNG</h5>
        <p><b>2002</b> – HTL - Matura mit Schwerpunkt IT und Betrieblicher Organisation</p>
        <p><b>2009</b> - Studium BWL mit Schwerpunkten Banking &amp; Finance sowie Kapitalmärkte</p>
        <p><b>2012</b> – Buchhalter &amp; Bilanzbuchhalterprüfung</p>
        <p><b>2013</b> – Angelobung zum Steuerberater</p>
      </div>
      <div class="cv-box"><h5>BERUFLICHER WERDEGANG</h5>
        <p><b>2003 - 2009</b> – Selbstständig tätig im IT Sektor</p>
        <p><b>Seit 2009</b> – Beratend tätig in der Steuerberatung / Wirtschaftsprüfung in verschiedenen Kanzleien. Zuletzt in leitender Funktion bei Alpenberg Prüfung Tirol</p>
        <p><b>2022</b>: Gründung der eigenen Kanzlei LM-Steuerberatung mit Fokus Krypto-Beratung.</p>
      </div>
    </div>
    <span class="btn-solid">Zum Online-Profil <span class="dot-arrow" style="color:#fff"></span></span>
  </div>
  <footer class="footer">
    <div class="foot-grid">
      <div class="foot-brand"><div class="brand"><i></i>LM STEUERBERATUNG</div><p>Ihrem Spezialisten bei allen steuerlichen Themen rund um Einkünfte &amp; Vermögen aus Krypto-Assets.</p><div class="social"><i></i><i></i><i></i></div></div>
      <div class="foot-col"><h4>QUICK LINKS</h4><ul><li>Home</li><li>Leistungen</li><li>Über mich</li><li>Impressum</li><li>Kontakt</li></ul></div>
      <div class="foot-col"><h4>CONTACT US</h4><ul><li><svg viewBox="0 0 10 10"><rect y="2" width="10" height="6.5" fill="#fff"/></svg>office@lm-steuer.example</li><li><svg viewBox="0 0 10 10"><path fill="#fff" d="M2 1l2 2-1 1.3c.6 1.2 1.5 2.1 2.7 2.7L7 6l2 2-1.2 1.3C4.5 9 1 5.5.7 2.2z"/></svg>+43 512 000 417</li></ul></div>
    </div>
    <div class="copy">© 2022 <b>LM-Steuerberatung</b>. All right reserved</div>
  </footer>
</section>

<div class="thanks">
  <div class="t1">Thank You</div>
  <div class="t2">For Watching</div>
</div>

</body>
</html>
```